Meadowlark Property Review is a leading provider of residential appraisal and home inspection products in S

I need a business card/logo designed that obviously describes my business. We are a residential appraisal and home inspection company in Springfield, MO. We offer residential appraisals, home inspection, pest inspection and radon gas measurement. We have been in business for 18 years and hold state certified residential appraisal licenses and OBREX certified home inspection licenses. I have a logo that I really like and will attach, but would be open to new suggestions. I like more modern designs than traditional and would like a two sided card with our services, licenses and qualifications on the back.

```html
<!DOCTYPE html>
<html lang="en">
<head>
<meta charset="utf-8">
<title>Meadowlark Property Review – Business Card</title>
<link rel="stylesheet" href="https://fonts.googleapis.com/css2?family=Arimo:wght@400;700&display=swap">
<style>
  :root {
    --canvas: #ece7df;
    --brown: #9a774c;
    --brown-dark: #8a6a43;
    --brown-light: #b08c60;
    --orange: #f5981f;
    --white: #ffffff;
    --logo-brown: #8c6a45;
  }
  * { box-sizing: border-box; margin: 0; padding: 0; }
  html, body {
    width: 1200px; height: 892px; overflow: hidden;
    background: var(--canvas);
    font-family: "Arimo", Arial, sans-serif;
  }
  .sheet {
    width: 1200px; height: 892px;
    display: flex; align-items: center; justify-content: center; gap: 34px;
  }
  .card {
    position: relative;
    width: 560px; height: 320px;
    overflow: hidden;
    box-shadow: 0 6px 18px rgba(60, 40, 20, .22);
  }

  /* ---------- Front ---------- */
  .card-front { background: var(--brown); color: var(--white); }
  .front-shape { position: absolute; inset: 0; }
  .front-brand {
    position: absolute; left: 150px; top: 62px; width: 320px;
    text-align: center; color: var(--logo-brown);
    font-weight: 700; line-height: 1;
  }
  .front-brand .brand-main { display: block; font-size: 44px; letter-spacing: -0.5px; }
  .front-brand .brand-sub { display: block; font-size: 19px; letter-spacing: 6px; margin-top: 8px; }
  .contact-left {
    position: absolute; left: 22px; top: 220px;
    font-size: 15px; line-height: 22px;
  }
  .contact-right {
    position: absolute; right: 18px; top: 246px;
    font-size: 15px; line-height: 21px; text-align: right;
  }
  .contact-row { display: flex; align-items: center; gap: 9px; }
  .contact-right .contact-row { justify-content: flex-end; }
  .contact-icon { width: 15px; height: 15px; flex: none; }
  .address {
    position: absolute; left: 22px; right: 18px; bottom: 9px;
    font-size: 13px; white-space: nowrap;
  }

  /* ---------- Back ---------- */
  .card-back {
    background: linear-gradient(120deg, var(--brown-dark) 0%, var(--brown) 55%, var(--brown-light) 100%);
    color: var(--white);
  }
  .service-list {
    position: absolute; right: 232px; top: 22px;
    list-style: none; text-align: right;
    font-size: 15.5px; line-height: 25px;
  }
  .service-list li { display: flex; align-items: center; justify-content: flex-end; gap: 12px; }
  .service-mark { width: 10px; height: 10px; flex: none; }
  .divider { position: absolute; inset: 0; pointer-events: none; }
  .back-brand {
    position: absolute; left: 345px; top: 118px; width: 200px;
    text-align: center; font-weight: 700; line-height: 1;
  }
  .back-brand .brand-main { display: block; font-size: 32px; letter-spacing: -0.5px; }
  .back-brand .brand-sub { display: block; font-size: 14px; letter-spacing: 4px; margin-top: 8px; }
</style>
</head>
<body>
<main class="sheet">

  <!-- Front side -->
  <section class="card card-front" aria-label="Card front">
    <svg class="front-shape" viewBox="0 0 560 320" width="560" height="320" aria-hidden="true">
      <path fill="var(--orange)" d="M22,0 C46,170 140,222 260,232 C360,240 450,228 520,206 C450,220 360,228 260,218 C140,205 70,150 48,0 Z"/>
      <path fill="var(--white)" d="M40,0 H560 V190 C470,215 360,228 260,218 C140,205 70,150 48,0 Z"/>
    </svg>

    <div class="front-brand">
      <span class="brand-main">Meadowlark</span>
      <span class="brand-sub">PROPERTY REVIEW</span>
    </div>

    <div class="contact-left">
      <div class="contact-row">
        <svg class="contact-icon" viewBox="0 0 15 15" aria-hidden="true"><rect x="0.5" y="0.5" width="14" height="14" fill="none" stroke="#fff"/><rect x="3" y="6" width="9" height="6" fill="#fff"/><rect x="4" y="3" width="7" height="2" fill="#fff"/></svg>
        <span>417-555-0142</span>
      </div>
      <div class="contact-row">
        <svg class="contact-icon" viewBox="0 0 15 15" aria-hidden="true"><path d="M4,2 L6,2 L7,5 L5.5,6 Q7,9 9,9.5 L10,8 L13,9 L13,11 Q12,13 10,12.5 Q4,10.5 2.5,4 Q2.5,2.5 4,2 Z" fill="#fff"/></svg>
        <span>417-555-0187</span>
      </div>
    </div>

    <div class="contact-right">
      <div class="contact-row">
        <span>417-555-0163</span>
        <svg class="contact-icon" viewBox="0 0 15 15" aria-hidden="true"><rect x="0.5" y="0.5" width="14" height="14" fill="none" stroke="#fff"/><rect x="3" y="6" width="9" height="6" fill="#fff"/><rect x="4" y="3" width="7" height="2" fill="#fff"/></svg>
      </div>
      <div class="contact-row">
        <span>info@meadowlarkreview.com</span>
        <svg class="contact-icon" viewBox="0 0 15 15" aria-hidden="true"><rect x="0.5" y="0.5" width="14" height="14" fill="none" stroke="#fff"/><rect x="2.5" y="4" width="10" height="7" fill="none" stroke="#fff"/><path d="M2.5,4 L7.5,8 L12.5,4" fill="none" stroke="#fff"/></svg>
      </div>
    </div>

    <p class="address">Meadowlark Property Review, 4410 S Linden Avenue; Suite C Springfield, MO 65810</p>
  </section>

  <!-- Back side -->
  <section class="card card-back" aria-label="Card back">
    <ul class="service-list">
      <li>Home inspection<svg class="service-mark" viewBox="0 0 10 10" aria-hidden="true"><circle cx="5" cy="5" r="4" fill="none" stroke="#fff"/><circle cx="5" cy="5" r="1.6" fill="#fff"/></svg></li>
      <li>Property inspection<svg class="service-mark" viewBox="0 0 10 10" aria-hidden="true"><circle cx="5" cy="5" r="4" fill="none" stroke="#fff"/><circle cx="5" cy="5" r="1.6" fill="#fff"/></svg></li>
      <li>Residential appraisal<svg class="service-mark" viewBox="0 0 10 10" aria-hidden="true"><circle cx="5" cy="5" r="4" fill="none" stroke="#fff"/><circle cx="5" cy="5" r="1.6" fill="#fff"/></svg></li>
      <li>Termite inspection<svg class="service-mark" viewBox="0 0 10 10" aria-hidden="true"><circle cx="5" cy="5" r="4" fill="none" stroke="#fff"/><circle cx="5" cy="5" r="1.6" fill="#fff"/></svg></li>
      <li>Radon gas measurement<svg class="service-mark" viewBox="0 0 10 10" aria-hidden="true"><circle cx="5" cy="5" r="4" fill="none" stroke="#fff"/><circle cx="5" cy="5" r="1.6" fill="#fff"/></svg></li>
      <li>Pre purchase inspection<svg class="service-mark" viewBox="0 0 10 10" aria-hidden="true"><circle cx="5" cy="5" r="4" fill="none" stroke="#fff"/><circle cx="5" cy="5" r="1.6" fill="#fff"/></svg></li>
      <li>Thermal imaging<svg class="service-mark" viewBox="0 0 10 10" aria-hidden="true"><circle cx="5" cy="5" r="4" fill="none" stroke="#fff"/><circle cx="5" cy="5" r="1.6" fill="#fff"/></svg></li>
      <li>Mechanical inspection<svg class="service-mark" viewBox="0 0 10 10" aria-hidden="true"><circle cx="5" cy="5" r="4" fill="none" stroke="#fff"/><circle cx="5" cy="5" r="1.6" fill="#fff"/></svg></li>
      <li>Tax appeal<svg class="service-mark" viewBox="0 0 10 10" aria-hidden="true"><circle cx="5" cy="5" r="4" fill="none" stroke="#fff"/><circle cx="5" cy="5" r="1.6" fill="#fff"/></svg></li>
      <li>Asset evaluation<svg class="service-mark" viewBox="0 0 10 10" aria-hidden="true"><circle cx="5" cy="5" r="4" fill="none" stroke="#fff"/><circle cx="5" cy="5" r="1.6" fill="#fff"/></svg></li>
      <li>Energy audits<svg class="service-mark" viewBox="0 0 10 10" aria-hidden="true"><circle cx="5" cy="5" r="4" fill="none" stroke="#fff"/><circle cx="5" cy="5" r="1.6" fill="#fff"/></svg></li>
    </ul>

    <svg class="divider" viewBox="0 0 560 320" width="560" height="320" aria-hidden="true">
      <line x1="348" y1="24" x2="322" y2="298" stroke="#fff" stroke-width="1.2" opacity=".9"/>
    </svg>

    <div class="back-brand">
      <span class="brand-main">Meadowlark</span>
      <span class="brand-sub">PROPERTY REVIEW</span>
    </div>
  </section>

</main>
</body>
</html>
```